2018 - 2019 Academic Program & Schedule ofEvents

10 page booklet listing upcoming courses for Sept 2018- May 2019
Program guide showing members what the courses are for the upcoming year.
It gives the course description & learning objectives & CE credits offered for each lecture. Also gives date, time location, intended participants, course description & learning objectives

Please use the KTRM 2016-2017 & 2017-2018 program guides as reference. We don't want to use any actual photo of Quimby, we would like something more modern and cleaner look like the above mentioned program guides.

Target Market(s)

Dentist

Industry/Entity Type

Dental

Font styles to use
Serif
Script

Colors
f37122

Requirements
Must have
• Must have our logo on front & back
• & "LOBU logo on back
• Table of contents, Course title, Date, location, intended audience, Time, Speaker's name & Title
Nice to have
• Harold Quimby quote

```html
<!DOCTYPE html>
<html lang="en">
<head>
<meta charset="utf-8">
<title>September Course – Restoring Dental Implants</title>
<link href="https://fonts.googleapis.com/css2?family=EB+Garamond:ital,wght@0,400;0,600;0,700;1,400&family=Montserrat:wght@300;400&display=swap" rel="stylesheet">
<style>
  :root {
    --orange: #f37122;
    --ink: #2b2b2b;
    --paper: #ffffff;
    --backdrop: #eeeae4;
    --badge: #d9d9d9;
  }
  * { box-sizing: border-box; margin: 0; padding: 0; }
  html, body { width: 1200px; height: 1200px; overflow: hidden; background: var(--backdrop); }
  .page {
    position: absolute; left: 218px; top: 40px; width: 763px; height: 1120px;
    background: var(--paper); color: var(--ink);
    font-family: "EB Garamond", Georgia, serif;
  }
  .month-band {
    position: absolute; left: 0; top: 41px; width: 361px; height: 80px;
    background: var(--orange); color: #fff;
    font-family: "Montserrat", Arial, sans-serif; font-weight: 300;
    font-size: 35px; letter-spacing: 1px; padding: 21px 0 0 40px;
  }
  .course-title {
    position: absolute; left: 40px; top: 158px; width: 330px;
    color: var(--orange); font-weight: 700; font-size: 24px; line-height: 28px;
  }
  .speaker { position: absolute; left: 40px; top: 244px; width: 340px; font-size: 17.6px; line-height: 22.3px; }
  .speaker-name { font-weight: 700; }
  .schedule {
    position: absolute; left: 40px; top: 401px;
    color: var(--orange); font-family: "Montserrat", Arial, sans-serif;
    font-size: 18.5px; line-height: 23.5px; letter-spacing: 0.3px;
  }
  .details { position: absolute; left: 401px; top: 42px; width: 322px; font-size: 14.6px; line-height: 19.2px; }
  .details h3 { color: var(--orange); font-size: 15.5px; font-weight: 700; line-height: 18px; margin-top: 19px; }
  .details h3:first-child { margin-top: 0; }
  .details p { text-align: justify; }
  .objectives { list-style: none; }
  .objectives li { position: relative; padding-left: 21px; text-align: justify; }
  .objectives li::before { content: "•"; position: absolute; left: 0; }
  .credits { margin-top: 19px; }
  .footer-rule { position: absolute; left: 40px; top: 991px; width: 683px; height: 1px; background: var(--orange); }
  .page-number { position: absolute; left: 40px; top: 1030px; font-family: "Montserrat", Arial, sans-serif; font-size: 23px; }
  .partner-badge { position: absolute; left: 274px; top: 1018px; }
  .brand { position: absolute; left: 421px; top: 1030px; width: 302px; }
  .brand-mark { display: flex; align-items: center; gap: 8px; color: var(--orange); font-size: 22px; font-weight: 600; letter-spacing: 3px; }
  .brand-mark .square { width: 14px; height: 14px; background: var(--orange); }
  .brand-tagline { margin: 6px 0 0 0; font-style: italic; font-size: 10.5px; line-height: 15px; color: var(--ink); }
</style>
</head>
<body>
<main class="page">
  <div class="month-band">SEPTEMBER</div>

  <h1 class="course-title">Restoring Dental Implants: Current Prosthetic Options</h1>

  <div class="speaker">
    <p class="speaker-name">Dr. Daniel R. Ostrander</p>
    <p>Private practice in Montreal,<br>Canada limited to Prosthetics and Implant Dentistry. Assistant Clinical Professor, Division of Restorative Sciences,<br>at Harborview University</p>
  </div>

  <div class="schedule">
    <p>Wednesday, September 10, 2014</p>
    <p>7:30am Breakfast/Registration</p>
    <p>8:00am to 4:00pm Lecture</p>
  </div>

  <section class="details">
    <h3>Participants</h3>
    <p>Doctors and Clinical Staff</p>
    <h3>Location</h3>
    <p>Maplewood Country Club 4820 Fairhaven Road, Brookfield, NJ 08712</p>
    <h3>Description</h3>
    <p>The use of implant supported single tooth and partial edentulous restorations in the anterior and posterior zone covers a wide variety of clinical situations. Provisional replacement of teeth and the high expectations of esthetics and function create daily challenges in our practices. Immediate and early loading protocols and management options will be explored as well.</p>
    <p>The emergence of high performance ceramic materials is providing a new set of options to restorative dentists. A detailed analysis of restorative material options will be discussed.</p>
    <p>The treatment planning and clinical processes used to create successful outcomes will be presented along with the workflow technologies as they relate to successful long term performance of implant therapy in daily clinical practice.</p>
    <h3>Learning Objectives</h3>
    <p>At the completion of this course, participants will be able to:</p>
    <ul class="objectives">
      <li>Understand the treatment planning and execution of single tooth and partial edentulous anterior and posterior restorations</li>
      <li>Understand how to select abutments for screw retained and cement retained restorations</li>
      <li>Understand immediate and early loading protocols</li>
      <li>Understand the impact of high performance ceramic materials and digital technology workflow</li>
    </ul>
    <p class="credits">Credits: Seven CEU</p>
  </section>

  <div class="footer-rule"></div>
  <div class="page-number">01</div>

  <svg class="partner-badge" width="70" height="80" viewBox="0 0 70 80" role="img" aria-label="Continuing education approval badge">
    <rect x="0" y="0" width="70" height="80" fill="var(--badge)"/>
  </svg>

  <div class="brand">
    <div class="brand-mark"><span class="square"></span><span>KTRM</span></div>
    <p class="brand-tagline">Excellence through Dental Education<br>A Northwind Study Club</p>
  </div>
</main>
</body>
</html>
```